English and Spanish Language School Needs a Business Card

Need a business card design a startup company called Maribel Language School. The company will offer English and Spanish conversational level courses designed to make the learner feel comfortable with grammar and vocabulary. We would like to see a logo with some colour that should communicate learning, growth.

Target Market(s)

Consumers and businesses

Industry/Entity Type

Education

Contact Information for Business Card

TBD

Font styles to use
Serif

Requirements
Must have
• Include the following
• Logo
• Name
• Title
• Cellphone Number
• Office Phone number
• Email address
• Office Address

```html
<!DOCTYPE html>
<html lang="en">
<head>
<meta charset="utf-8">
<title>Maribel Language School – Business Card</title>
<link rel="stylesheet" href="https://fonts.googleapis.com/css2?family=Open+Sans:wght@400;700&family=Ubuntu:wght@500&display=swap">
<style>
  :root {
    --page-bg: #3a332f;
    --card-bg: #111111;
    --card-edge: #1c1c1c;
    --brand-red: #e2313f;
    --brand-teal: #14a8b5;
    --text-light: #f2f2f2;
    --foil-silver: #cfcfcf;
  }
  * { margin: 0; padding: 0; box-sizing: border-box; }
  html, body { width: 1200px; height: 900px; overflow: hidden; }
  body {
    background: var(--page-bg);
    font-family: "Open Sans", Arial, sans-serif;
    position: relative;
  }
  .card {
    position: absolute;
    top: 290px;
    width: 520px;
    height: 300px;
    background: var(--card-bg);
    border: 1px solid var(--card-edge);
    box-shadow: 0 10px 30px rgba(0,0,0,.45);
  }
  .card--front { left: 60px; }
  .card--back { left: 620px; }

  .brand {
    font-family: "Ubuntu", "Open Sans", sans-serif;
    font-weight: 500;
    line-height: 1.05;
  }
  .card--front .brand {
    position: absolute;
    left: 34px;
    top: 118px;
    width: 200px;
    color: var(--brand-red);
    font-size: 30px;
  }
  .brand__tagline { display: block; font-size: 19px; }

  .divider {
    position: absolute;
    left: 240px;
    top: 50px;
    width: 1px;
    height: 200px;
    background: linear-gradient(to bottom, transparent, var(--brand-red) 35%, var(--brand-red) 65%, transparent);
  }

  .contact {
    position: absolute;
    left: 262px;
    top: 58px;
    color: var(--text-light);
    font-size: 13.5px;
    line-height: 1.3;
  }
  .contact__name { font-weight: 700; font-size: 15px; }
  .contact__first { color: var(--brand-red); }
  .contact__last { color: var(--brand-teal); }
  .contact__address { margin-top: 14px; }
  .contact__list { list-style: none; margin-top: 14px; }
  .contact__list li { display: flex; align-items: center; gap: 8px; }
  .contact__list svg { width: 10px; height: 10px; fill: var(--brand-red); flex: none; }

  .card--back .brand {
    position: absolute;
    left: 0; right: 0;
    top: 110px;
    text-align: center;
    color: var(--foil-silver);
    font-size: 44px;
  }
  .card--back .brand__tagline { font-size: 22px; margin-top: 4px; }
</style>
</head>
<body>
  <section class="card card--front" aria-label="Business card front">
    <div class="brand">Maribel<span class="brand__tagline">Language School</span></div>
    <div class="divider"></div>
    <div class="contact">
      <p class="contact__name"><span class="contact__first">Daniel</span> <span class="contact__last">Moreno</span></p>
      <p class="contact__title">Managing Director</p>
      <p class="contact__address">48 Alder Street<br>Dunmore Vale, 204817.</p>
      <ul class="contact__list">
        <li><svg viewBox="0 0 10 10" aria-hidden="true"><path d="M2 0.5l1.6 2.2-1 1a6 6 0 0 0 3.7 3.7l1-1L9.5 8 8.2 9.5C4 9.5 .5 6 .5 1.8z"/></svg>055-210 384 617</li>
        <li><svg viewBox="0 0 10 10" aria-hidden="true"><path d="M2.5 0h5v10h-5zM3.3 1v7h3.4V1zM4.5 8.5h1v.8h-1z" fill-rule="evenodd"/></svg>hello@maribelschool.com</li>
        <li><svg viewBox="0 0 10 10" aria-hidden="true"><path d="M0 2h10v6H0zM.8 2.6L5 5.6l4.2-3z" fill-rule="evenodd"/></svg>www.maribelschool.com</li>
      </ul>
    </div>
  </section>

  <section class="card card--back" aria-label="Business card back">
    <div class="brand">Maribel<span class="brand__tagline">Language School</span></div>
  </section>
</body>
</html>
```